Local Roofing/Construction company business needs new biz card design

We need a new business card design, current cards are from the start of this operation and generic at best. We are a local Construction Company (General Contractor) with a majority of our work originating from insurance claims-exterior finish work is the main focus (Roofs-Siding-Gutters etc). Heavily involved with homeowners and the low ball offers they receive from insurance company's after a insurable event takes place. I have attached some of our original logo file(s) below.

```html
<!DOCTYPE html>
<html lang="en">
<head>
<meta charset="utf-8">
<title>Halden Build Co — Business Card</title>
<link href="https://fonts.googleapis.com/css2?family=Montserrat:wght@400;500;700;800&display=swap" rel="stylesheet">
<style>
  :root {
    --backdrop: #e1e3e3;
    --paper: #fbfbfb;
    --brand-green: #1f8a3a;
    --ink-grey: #4a4a4a;
    --edge: #1f8a3a;
  }
  * { margin: 0; padding: 0; box-sizing: border-box; }
  html, body {
    width: 1200px; height: 829px; overflow: hidden;
    background: var(--backdrop);
    font-family: "Montserrat", sans-serif;
  }
  .stage {
    position: relative; width: 1200px; height: 829px;
    display: flex; align-items: center; justify-content: center; gap: 50px;
  }
  .card {
    position: relative; width: 520px; height: 300px;
    background: var(--paper);
    border-bottom: 4px solid var(--edge);
    box-shadow: 0 10px 24px rgba(0,0,0,0.12);
    overflow: hidden;
  }
  /* front */
  .front .side-tab {
    position: absolute; left: 0; top: 64px; width: 8px; height: 22px;
    background: var(--brand-green);
  }
  .front .wordmark {
    position: absolute; left: 30px; top: 22px;
    display: flex; align-items: center; gap: 10px;
    color: var(--brand-green); font-weight: 800; font-size: 22px;
    letter-spacing: 1px; text-transform: uppercase;
  }
  .wordmark .mark-square {
    width: 18px; height: 18px; background: var(--brand-green);
  }
  .front .identity { position: absolute; left: 30px; top: 66px; }
  .identity .person-name {
    color: var(--brand-green); font-weight: 700; font-size: 17px;
    letter-spacing: 1.6px; text-transform: uppercase;
  }
  .identity .role { color: var(--ink-grey); font-size: 11px; margin-top: 2px; }
  .identity .address {
    color: var(--ink-grey); font-size: 12.5px; line-height: 1.45; margin-top: 10px;
  }
  .contact-list { list-style: none; margin-top: 10px; }
  .contact-list li {
    display: flex; align-items: center; gap: 8px;
    color: var(--ink-grey); font-size: 12.5px; line-height: 1.75;
  }
  .contact-list svg { width: 11px; height: 11px; flex: none; }
  .front .corner-block {
    position: absolute; right: 40px; bottom: -20px;
    width: 170px; height: 170px; background: var(--brand-green);
  }
  /* back */
  .back { display: flex; align-items: center; justify-content: center; }
  .back .wordmark-large {
    display: flex; align-items: center; gap: 12px;
    color: var(--brand-green); font-weight: 800; font-size: 30px;
    letter-spacing: 1.5px; text-transform: uppercase;
  }
  .wordmark-large .mark-square { width: 24px; height: 24px; background: var(--brand-green); }
</style>
</head>
<body>
<main class="stage">
  <section class="card front" aria-label="Business card front">
    <span class="side-tab"></span>
    <div class="wordmark"><span class="mark-square"></span>Halden Build Co</div>
    <div class="identity">
      <p class="person-name">Marcus Ellery</p>
      <p class="role">Managing Director</p>
      <p class="address">418 Birchwood Avenue<br>Harlow County 5147</p>
      <ul class="contact-list">
        <li><svg viewBox="0 0 12 12"><circle cx="6" cy="6" r="6" fill="#1f8a3a"/><path d="M4 3.2l1 1.4-.6.7c.4.9 1.1 1.6 2 2l.7-.6 1.4 1-.5 1c-2.3-.2-4.3-2.2-4.6-4.6z" fill="#fff"/></svg>0491 552 706</li>
        <li><svg viewBox="0 0 12 12"><circle cx="6" cy="6" r="6" fill="#1f8a3a"/><rect x="3" y="4" width="6" height="4.2" fill="#fff"/><path d="M3 4l3 2.3L9 4" stroke="#1f8a3a" stroke-width=".7" fill="none"/></svg>info@haldenbuild.com</li>
        <li><svg viewBox="0 0 12 12"><circle cx="6" cy="6" r="6" fill="#1f8a3a"/><circle cx="6" cy="6" r="3" stroke="#fff" stroke-width=".8" fill="none"/><path d="M3 6h6M6 3v6" stroke="#fff" stroke-width=".6"/></svg>www.haldenbuild.com</li>
      </ul>
    </div>
    <span class="corner-block"></span>
  </section>

  <section class="card back" aria-label="Business card back">
    <div class="wordmark-large"><span class="mark-square"></span>Halden Build Co</div>
  </section>
</main>
</body>
</html>
```